Looking for a modern, Professional business card design

We have a simple business card, but are looking for a more modern, professional look. A sample of the basic card is attached as well as the logo. We would also like to add that we offer:
Struggling with your finances?
- Learn to become debt free
- Discover the power of cash
- Control your money instead of it controlling you
Let us help you achieve a new level of financial freedom!
Also, we would like to have a "SPECIAL OFFER!: FREE 30 minute consultation"
Financial Planning

```html
<!DOCTYPE html>
<html lang="en">
<head>
<meta charset="utf-8">
<title>Steadypath Financial Coaching – Business Card</title>
<link href="https://fonts.googleapis.com/css2?family=Roboto:wght@400;700;900&display=swap" rel="stylesheet">
<style>
  :root {
    --stage: #e9eaec;
    --ink: #111111;
    --paper: #ffffff;
    --green-dark: #3f9a2a;
    --green: #6cbf3c;
    --green-light: #a6d96a;
    --muted: #2b2b2b;
  }
  * { box-sizing: border-box; margin: 0; padding: 0; }
  html, body { width: 1200px; height: 950px; overflow: hidden; }
  body {
    background: var(--stage);
    font-family: "Roboto", Arial, sans-serif;
    position: relative;
  }
  .card {
    position: absolute;
    width: 700px;
    height: 400px;
    border-radius: 6px;
    overflow: hidden;
    box-shadow: 0 8px 24px rgba(0,0,0,.18);
  }

  /* Back side */
  .card-back {
    left: 60px; top: 60px;
    background: var(--ink);
    color: var(--paper);
    text-align: center;
  }
  .card-back .brand {
    margin-top: 62px;
    display: inline-flex;
    align-items: center;
    gap: 14px;
    font-weight: 900;
    font-size: 34px;
    letter-spacing: 2px;
  }
  .brand-dot {
    width: 22px; height: 22px; border-radius: 50%;
    background: var(--paper);
  }
  .offer-block { margin-top: 52px; }
  .offer-heading { font-weight: 700; font-size: 19px; letter-spacing: .5px; }
  .offer-lines { margin-top: 6px; font-size: 16px; line-height: 1.4; }
  .offer-special { margin-top: 6px; font-weight: 700; font-size: 19px; }

  /* Front side */
  .card-front {
    left: 440px; top: 490px;
    background: var(--paper);
  }
  .front-shape { position: absolute; inset: 0; }
  .front-brand {
    position: absolute;
    left: 48px; top: 168px;
    display: flex; align-items: center; gap: 12px;
  }
  .front-brand .brand-dot { background: var(--green); width: 26px; height: 26px; }
  .front-brand .brand-name {
    font-weight: 900;
    font-size: 30px;
    letter-spacing: 1px;
    color: var(--ink);
    line-height: 1.05;
  }
  .contact {
    position: absolute;
    right: 34px; top: 112px;
    text-align: right;
    color: var(--paper);
  }
  .contact-name { font-weight: 700; font-size: 21px; }
  .contact-role { font-size: 17px; margin-top: 4px; }
  .contact-list { list-style: none; margin-top: 26px; font-size: 15px; line-height: 1.75; }
  .contact-list li { display: flex; justify-content: flex-end; align-items: center; gap: 8px; }
  .contact-list svg { width: 15px; height: 15px; flex: none; }
</style>
</head>
<body>

<section class="card card-back" aria-label="Card back">
  <div class="brand"><span class="brand-dot"></span><span>STEADYPATH</span></div>
  <div class="offer-block">
    <p class="offer-heading">STRUGGLING WITH YOUR FINANCES?</p>
    <p class="offer-lines">
      Learn to become debt free • Discover the power of cash<br>
      Control your money instead of it controlling you<br>
      Let us help you achieve a new level of financial freedom!
    </p>
    <p class="offer-special">SPECIAL OFFER!: FREE 30 minute consultation</p>
  </div>
</section>

<section class="card card-front" aria-label="Card front">
  <svg class="front-shape" viewBox="0 0 700 400" preserveAspectRatio="none" aria-hidden="true">
    <defs>
      <radialGradient id="greenPanel" cx="75%" cy="35%" r="70%">
        <stop offset="0" stop-color="var(--green-light)"/>
        <stop offset=".55" stop-color="var(--green)"/>
        <stop offset="1" stop-color="var(--green-dark)"/>
      </radialGradient>
    </defs>
    <path d="M448 0 C360 110 340 280 396 400 L700 400 L700 0 Z" fill="var(--ink)"/>
    <path d="M468 0 C384 110 368 280 420 400 L700 400 L700 0 Z" fill="url(#greenPanel)"/>
  </svg>

  <div class="front-brand">
    <span class="brand-dot"></span>
    <span class="brand-name">STEADYPATH</span>
  </div>

  <div class="contact">
    <p class="contact-name">Daniel R. Hayes</p>
    <p class="contact-role">Personal Financial Coach</p>
    <ul class="contact-list">
      <li>(205) 555-0148
        <svg viewBox="0 0 16 16"><rect x="4" y="1" width="8" height="14" rx="1.5" fill="none" stroke="#fff" stroke-width="1.6"/></svg>
      </li>
      <li>daniel@steadypathcoaching.com
        <svg viewBox="0 0 16 16"><rect x="1" y="3" width="14" height="10" fill="#fff"/><path d="M1 3 L8 9 L15 3" fill="none" stroke="#3f9a2a" stroke-width="1.3"/></svg>
      </li>
      <li>www.steadypathcoaching.com
        <svg viewBox="0 0 16 16"><circle cx="8" cy="8" r="6.5" fill="none" stroke="#fff" stroke-width="1.5"/><path d="M1.5 8 H14.5 M8 1.5 C5 5 5 11 8 14.5 M8 1.5 C11 5 11 11 8 14.5" fill="none" stroke="#fff" stroke-width="1.1"/></svg>
      </li>
    </ul>
  </div>
</section>

</body>
</html>
```